Business Card Design For A Renovation Contractor Company

We need a business card for a new company based in Singapore, our company name is "RB Tolvane". We are a renovation contractor that builds designs into reality. We build more of F&B restaurants, retail stores and commercial offices. We work very closely with designers. The final design should communicate to our client that we are a company that you can trust, that will plan and complete your project without giving you a headache. I like my client to remember my company as "RB". The beauty of SIMPLE is important.

Industry/Entity Type

Contractor

Requirements
Nice to have
• Black or Red base

```html
<!DOCTYPE html>
<html lang="en">
<head>
<meta charset="utf-8">
<title>RB Tolvane — Business Card</title>
<link rel="stylesheet" href="https://fonts.googleapis.com/css2?family=Questrial&family=Open+Sans:wght@400;700&display=swap">
<style>
  :root {
    --canvas-bg: #e9e7e4;
    --card-white: #ffffff;
    --ink: #1a1a1a;
    --brand-red: #d7191f;
    --panel-black: #0d0d0d;
    --panel-text: #f2f2f2;
    --rule-grey: #3a3a3a;
    --ghost: #f3e9ea;
    --ghost-line: #ecd9db;
  }
  * { margin: 0; padding: 0; box-sizing: border-box; }
  html, body { width: 1200px; height: 720px; overflow: hidden; }
  body {
    background: var(--canvas-bg);
    display: flex;
    align-items: center;
    justify-content: center;
    gap: 40px;
    font-family: "Open Sans", Arial, sans-serif;
  }
  .card {
    position: relative;
    width: 540px;
    height: 309px;
    background: var(--card-white);
    overflow: hidden;
    box-shadow: 0 2px 10px rgba(0,0,0,0.12);
  }
  .card-art { position: absolute; inset: 0; width: 100%; height: 100%; }

  /* Brand lockup */
  .lockup { position: absolute; color: var(--ink); font-family: "Questrial", "Century Gothic", sans-serif; }
  .lockup-name { line-height: 1; letter-spacing: -0.5px; white-space: nowrap; }
  .lockup-rule { height: 1.5px; background: var(--rule-grey); margin-top: 4px; }
  .lockup-tagline { letter-spacing: 0.6px; line-height: 1.2; white-space: nowrap; }

  .front .lockup { left: 44px; top: 120px; width: 250px; }
  .front .lockup-name { font-size: 40px; }
  .front .lockup-tagline { font-size: 15.5px; }
  .front .mark-circle {
    position: absolute; left: 78px; top: 56px;
    width: 56px; height: 56px; border-radius: 50%;
    border: 4px solid var(--brand-red);
  }

  /* Contact panel */
  .contact-panel {
    position: absolute; left: 388px; top: 22px; width: 136px;
    color: var(--panel-text); font-size: 10.5px; line-height: 1.45;
  }
  .holder-name { font-weight: 700; font-size: 14px; text-align: right; line-height: 1.2; }
  .holder-title { text-align: right; font-size: 10.5px; margin-bottom: 12px; }
  .contact-list { list-style: none; }
  .contact-list li { display: flex; align-items: center; gap: 5px; white-space: nowrap; }
  .contact-list svg { width: 9px; height: 9px; flex: none; fill: var(--panel-text); }
  .address { margin-top: 10px; white-space: nowrap; }

  /* Back */
  .back .ghost-circle {
    position: absolute; left: 180px; top: 38px;
    width: 190px; height: 190px; border-radius: 50%;
    background: var(--ghost); border: 10px solid var(--ghost-line);
  }
  .back .lockup { left: 120px; top: 112px; width: 316px; }
  .back .lockup-name { font-size: 50px; }
  .back .lockup-tagline { font-size: 19px; }
  .web-address {
    position: absolute; left: 0; right: 0; bottom: 40px;
    text-align: center; font-size: 13px; letter-spacing: 3px; color: var(--ink);
  }
  .web-address .accent { color: var(--brand-red); }
</style>
</head>
<body>

  <section class="card front" aria-label="Card front">
    <svg class="card-art" viewBox="0 0 540 309" aria-hidden="true">
      <path fill="var(--brand-red)" d="M318 0 Q420 150 300 309 L540 309 L540 0 Z"/>
      <path fill="var(--card-white)" d="M332 0 Q434 150 314 309 L540 309 L540 0 Z"/>
      <path fill="var(--panel-black)" d="M338 0 Q440 150 320 309 L540 309 L540 0 Z"/>
    </svg>

    <div class="mark-circle"></div>
    <div class="lockup">
      <div class="lockup-name">RB Tolvane</div>
      <div class="lockup-rule"></div>
      <div class="lockup-tagline">crafting spaces, done right</div>
    </div>

    <div class="contact-panel">
      <div class="holder-name">Your Name</div>
      <div class="holder-title">Title</div>
      <ul class="contact-list">
        <li><svg viewBox="0 0 10 10"><path d="M2 0.5 L4 2.5 L3 3.8 Q4.5 6 6.2 7 L7.5 6 L9.5 8 L8 9.6 Q2 8.5 0.4 2 Z"/></svg>123-456-0789</li>
        <li><svg viewBox="0 0 10 10"><rect x="2.5" y="0" width="5" height="10" rx="1"/></svg>123-456-0789</li>
        <li><svg viewBox="0 0 10 10"><rect x="0" y="1.5" width="10" height="7" rx="1"/></svg>info@rbtolvane.com</li>
        <li><svg viewBox="0 0 10 10"><circle cx="5" cy="5" r="4.5"/></svg>www.rbtolvane.com</li>
      </ul>
      <div class="address">Street Name, City Name<br>State Zip Code</div>
    </div>
  </section>

  <section class="card back" aria-label="Card back">
    <div class="ghost-circle"></div>
    <div class="lockup">
      <div class="lockup-name">RB Tolvane</div>
      <div class="lockup-rule"></div>
      <div class="lockup-tagline">crafting spaces, done right</div>
    </div>
    <div class="web-address">www.<span class="accent">rbtolvane</span>.com</div>
  </section>

</body>
</html>
```